Social media app sign-up flow that asks users to give personal info and connect with other apps

Design an interactive, fun, and playful sign-up flow in which you are providing information about you, your interests, and connecting with different API plug-ins such as Chatterloop, Workvine, Tunevale, etc. (using the brand palette attached).

Basic wireframe, and business requirements are also attached.

Target Market(s)

Gen Z + Millennials (ages 22-40)

Font styles to use
Sans Serif

Colors
fbed22
fbee3d
fbf289

Requirements
Must have
• Forms for users to submit their info. Follow the color palette attached.

Connect with Chatterloop, Connect with Workvine, Connect with Tunevale, Connect with Gatherpost buttons
Nice to have
• I like the way you can use cards to submit your information for each category. Interactive card design for providing your info
Should not have
• Basic outdated designs, long forms

```html
<!DOCTYPE html>
<html lang="en">
<head>
<meta charset="utf-8">
<title>Sign-up Flow</title>
<link href="https://fonts.googleapis.com/css2?family=Quicksand:wght@500;600;700&display=swap" rel="stylesheet">
<style>
:root{
  --bg:#f3f4f6;
  --screen:#eef0f3;
  --panel:#f6f6f7;
  --orange:#ffa040;
  --yellow:#fdd23d;
  --gold:#fdc52c;
  --ink:#5b6173;
  --ink-soft:#8a8fa0;
  --line:#dfe1e6;
  --white:#ffffff;
  --chatter:#4a5f9a;
  --workvine:#0a73b1;
  --tunevale:#21b84f;
}
*{box-sizing:border-box;margin:0;padding:0}
html,body{width:1200px;height:2404px;overflow:hidden;background:var(--bg);font-family:"Quicksand",sans-serif;color:var(--ink)}
.screen{position:absolute;width:420px;height:1000px;background:var(--screen);border-radius:44px;overflow:hidden;box-shadow:0 10px 30px rgba(0,0,0,.08)}
.s1{left:104px;top:124px}.s2{left:668px;top:124px}.s3{left:104px;top:1252px}.s4{left:668px;top:1252px}
.hero{position:absolute;left:0;top:0;width:420px;height:335px;background:linear-gradient(160deg,var(--orange) 0%,var(--yellow) 45%,var(--orange) 100%)}
.panel-shape{position:absolute;left:0;top:0;width:420px;height:1000px}
.status{position:absolute;top:20px;left:34px;right:30px;display:flex;justify-content:space-between;color:var(--white);font-weight:700;font-size:17px}
.status svg{width:72px;height:14px}
.title{position:absolute;top:86px;width:100%;text-align:center;color:var(--white);font-weight:700;font-size:31px;letter-spacing:.5px}
.title.big{font-size:42px;top:78px}
.badge{position:absolute;left:140px;top:150px;width:140px;height:140px;border-radius:50%;background:var(--white);box-shadow:0 4px 14px rgba(0,0,0,.1);display:flex;align-items:center;justify-content:center}
.badge::before{content:"";position:absolute;inset:9px;border:2px solid var(--gold);border-radius:50%}
.badge svg{width:80px;height:80px}
.field-group{position:absolute;left:34px;top:322px;width:353px;height:110px;border:1px solid var(--line);border-radius:6px;background:var(--white)}
.field{height:55px;padding:9px 17px;font-size:16px;font-weight:600;position:relative}
.field+.field{border-top:1px solid var(--line);padding-top:16px}
.field small{display:block;font-size:12px;color:var(--ink-soft)}
.field .chev{position:absolute;right:18px;top:22px;width:12px;height:8px}
.note{position:absolute;left:38px;top:447px;width:345px;font-family:Arial,sans-serif;font-size:11.5px;line-height:22px;color:var(--ink)}
.continue{position:absolute;left:33px;top:509px;width:354px;height:51px;background:var(--gold);color:var(--white);font-weight:600;font-size:17px;display:flex;align-items:center;justify-content:center;border-radius:3px}
.or{position:absolute;left:34px;top:582px;width:353px;height:22px;text-align:center;font-size:17px}
.or::before,.or::after{content:"";position:absolute;top:11px;width:160px;border-top:1px solid var(--line)}
.or::before{left:0}.or::after{right:0}
.alt{position:absolute;left:34px;width:353px;height:49px;border:1px solid var(--line);border-radius:3px;background:var(--white);display:flex;align-items:center;font-size:15px;font-weight:600}
.alt .ico{width:44px;display:flex;justify-content:center;border-right:1px solid var(--line);height:16px;align-items:center;margin-right:13px}
.alt .ico i{display:block;width:10px;height:10px;border-radius:50%;background:var(--ink)}
.alt .ico svg{width:16px;height:12px}
.login{position:absolute;left:34px;top:870px;font-size:13.5px;font-weight:600}
.login u{color:var(--ink)}
.cards{position:absolute;left:49px;top:315px;display:grid;grid-template-columns:148px 148px;gap:18px 28px}
.card{height:135px;background:var(--white);border-radius:5px;box-shadow:0 2px 8px rgba(0,0,0,.06);display:flex;flex-direction:column;align-items:center;justify-content:flex-start;padding-top:16px;text-align:center;font-size:17px;font-weight:500;line-height:22px;color:var(--ink-soft)}
.card svg{width:60px;height:56px;margin-bottom:6px;fill:none;stroke:var(--ink-soft);stroke-width:1.8}
.chips{position:absolute;left:34px;top:326px;width:353px;display:grid;grid-template-columns:168px 168px;gap:9px 17px}
.chip{height:47px;border:1px solid var(--line);background:var(--white);display:flex;align-items:center;justify-content:space-between;gap:6px;padding:0 12px 0 13px;font-size:16px;font-weight:500;white-space:nowrap}
.chip.wide{grid-column:1/3}
.flag{width:25px;height:15px;display:block;flex-shrink:0}
.avatar{width:24px;height:24px;border-radius:50%;display:block;flex-shrink:0;background:#d7dae2}
.connect{position:absolute;left:35px;width:350px;height:54px;display:flex;align-items:center;justify-content:center;color:var(--white);font-size:19px;font-weight:600;border-radius:2px}
.connect i{width:20px;height:20px;border-radius:50%;background:var(--white);margin-right:14px;display:block}
.chatter{top:517px;background:var(--chatter)}
.workvine{top:582px;background:var(--workvine)}
.tunevale{top:582px;background:var(--tunevale);letter-spacing:.5px;font-size:18px}
.home{position:absolute;bottom:8px;left:132px;width:150px;height:5px;border-radius:3px;background:#5b6173}
</style>
</head>
<body>

<svg width="0" height="0" style="position:absolute">
  <defs>
    <symbol id="status" viewBox="0 0 72 14">
      <rect x="0" y="9" width="3" height="4" fill="#fff"/><rect x="5" y="6" width="3" height="7" fill="#fff"/><rect x="10" y="3" width="3" height="10" fill="#fff"/><rect x="15" y="0" width="3" height="13" fill="#fff"/>
      <path d="M25 5 Q32 -1 39 5 M28 8 Q32 4 36 8" stroke="#fff" stroke-width="2" fill="none"/><circle cx="32" cy="11" r="1.6" fill="#fff"/>
      <rect x="46" y="2" width="22" height="10" rx="2.5" stroke="#fff" stroke-width="1.3" fill="none"/><rect x="48" y="4" width="18" height="6" rx="1" fill="#fff"/><rect x="69" y="5" width="2" height="4" fill="#fff"/>
    </symbol>
    <symbol id="panel" viewBox="0 0 420 1000">
      <path d="M19 285 Q210 218 401 285 L401 930 L19 930 Z" fill="#f6f6f7"/>
    </symbol>
  </defs>
</svg>

<section class="screen s1">
  <div class="hero"></div>
  <svg class="panel-shape"><use href="#panel"/></svg>
  <div class="status"><span>9:41</span><svg><use href="#status"/></svg></div>
  <h1 class="title big">SIGN-UP</h1>
  <div class="badge"><svg viewBox="0 0 80 80" fill="none" stroke="#5b6173" stroke-width="4" stroke-linejoin="round"><circle cx="40" cy="40" r="34"/><path d="M30 24 L56 24 L56 56 L30 56"/><path d="M18 34 L34 34 L34 26 L48 40 L34 54 L34 46 L18 46 Z"/></svg></div>
  <div class="field-group">
    <div class="field"><small>Country /Region</small>United States (+1)<svg class="chev" viewBox="0 0 12 8"><path d="M1 1 L6 6 L11 1" stroke="#5b6173" stroke-width="1.6" fill="none"/></svg></div>
    <div class="field">Phone Number</div>
  </div>
  <p class="note">We'll call or text you to confirm your number.Standard message and data rates apply.</p>
  <div class="continue">CONTINUE</div>
  <div class="or">or</div>
  <div class="alt" style="top:630px"><span class="ico"><svg viewBox="0 0 16 12"><rect width="16" height="12" rx="1.5" fill="#5b6173"/><path d="M1 1 L8 7 L15 1" stroke="#fff" stroke-width="1.4" fill="none"/></svg></span>Continue with Email</div>
  <div class="alt" style="top:689px"><span class="ico"><i></i></span>Continue with Chatterloop</div>
  <div class="alt" style="top:748px"><span class="ico"><i></i></span>Continue With Searchly</div>
  <div class="alt" style="top:807px"><span class="ico"><i></i></span>Continue With Orchard</div>
  <p class="login">Already have an account? <u>Log in</u></p>
  <div class="home"></div>
</section>

<section class="screen s2">
  <div class="hero"></div>
  <svg class="panel-shape"><use href="#panel"/></svg>
  <div class="status"><span>9:41</span><svg><use href="#status"/></svg></div>
  <h1 class="title">TELL ME ABOUT YOU</h1>
  <div class="badge"><svg viewBox="0 0 80 80" fill="#5b6173"><circle cx="46" cy="14" r="8"/><path d="M30 32 L48 28 L40 62 Q44 62 50 56 L52 58 Q42 72 32 72 Q24 72 27 62 L33 38 L28 38 Z"/></svg></div>
  <div class="cards">
    <div class="card"><svg viewBox="0 0 60 56"><rect x="22" y="3" width="16" height="28" rx="8"/><path d="M16 22 Q16 38 30 38 Q44 38 44 22 M30 38 L30 48 M22 50 L38 50"/></svg>Places I've<br>Lived</div>
    <div class="card"><svg viewBox="0 0 60 56"><path d="M4 20 L30 9 L56 20 L30 31 Z M15 25 L15 38 Q30 46 45 38 L45 25 M52 22 L52 38"/></svg>Schools I've<br>Attended</div>
    <div class="card"><svg viewBox="0 0 60 56"><rect x="5" y="14" width="50" height="36"/><path d="M22 14 L22 7 L38 7 L38 14 M5 30 L55 30"/><rect x="27" y="27" width="6" height="7"/></svg>Places I've<br>Worked</div>
    <div class="card"><svg viewBox="0 0 60 56"><circle cx="18" cy="14" r="5"/><circle cx="42" cy="14" r="5"/><circle cx="30" cy="26" r="5"/><circle cx="10" cy="30" r="5"/><circle cx="50" cy="30" r="5"/><path d="M3 46 Q10 34 17 46 M23 46 Q30 34 37 46 M43 46 Q50 34 57 46"/></svg>People I<br>Know</div>
    <div class="card"><svg viewBox="0 0 60 56"><rect x="9" y="6" width="42" height="44"/><path d="M9 15 L51 15 M17 3 L17 9 M30 3 L30 9 M43 3 L43 9 M15 24 L22 24 M27 24 L34 24 M39 24 L46 24 M15 33 L22 33 M27 33 L34 33 M39 33 L46 33 M15 42 L22 42 M27 42 L34 42"/></svg>Events I've<br>Attended</div>
    <div class="card"><svg viewBox="0 0 60 56"><rect x="7" y="5" width="48" height="44"/><rect x="12" y="10" width="12" height="14"/><rect x="30" y="10" width="20" height="8"/><path d="M30 26 L50 26 M30 33 L50 33 M30 40 L50 40 M16 30 L16 52 M16 40 L24 40"/></svg>Events I'm<br>Attending</div>
    <div class="card"><svg viewBox="0 0 60 56"><ellipse cx="20" cy="44" rx="7" ry="5"/><ellipse cx="42" cy="38" rx="7" ry="5"/><path d="M27 44 L27 12 L49 4 L49 38 M27 20 L49 12"/></svg>Music I<br>Love</div>
    <div class="card"><svg viewBox="0 0 60 56"><path d="M30 50 L8 28 Q0 18 8 10 Q18 2 30 14 Q42 2 52 10 Q60 18 52 28 Z"/></svg>Teams I<br>Love</div>
  </div>
  <div class="home"></div>
</section>

<section class="screen s3">
  <div class="hero"></div>
  <svg class="panel-shape"><use href="#panel"/></svg>
  <div class="status"><span>9:41</span><svg><use href="#status"/></svg></div>
  <h1 class="title">PLACES I'VE LIVED</h1>
  <div class="badge"><svg viewBox="0 0 80 80" fill="none" stroke="#5b6173" stroke-width="3.5"><circle cx="36" cy="42" r="28"/><ellipse cx="36" cy="42" rx="12" ry="28"/><path d="M8 42 L64 42 M12 28 L60 28 M12 56 L60 56"/><path d="M58 36 Q46 22 46 14 Q46 4 58 4 Q70 4 70 14 Q70 22 58 36 Z" fill="#fff"/><circle cx="58" cy="14" r="4"/></svg></div>
  <div class="chips">
    <div class="chip">Chicago<i class="flag" role="img" aria-label="Chicago city flag" style="background:linear-gradient(#fff 30%,#7fc4ee 30% 40%,#fff 40% 60%,#7fc4ee 60% 70%,#fff 70%)"></i></div>
    <div class="chip">Madrid<i class="flag" role="img" aria-label="Flag of Spain" style="background:linear-gradient(#c60b1e 25%,#ffc400 25% 75%,#c60b1e 75%)"></i></div>
    <div class="chip">Paris<i class="flag" role="img" aria-label="Flag of France" style="background:linear-gradient(90deg,#002395 33%,#fff 33% 66%,#ed2939 66%)"></i></div>
    <div class="chip">Rio de Janiero<i class="flag" role="img" aria-label="Rio de Janeiro flag" style="background:linear-gradient(135deg,#5aa7e0,#fff,#5aa7e0)"></i></div>
    <div class="chip wide">London, United Kingdom<i class="flag" role="img" aria-label="Flag of the United Kingdom" style="background:linear-gradient(#012169 40%,#c8102e 40% 60%,#012169 60%)"></i></div>
  </div>
  <div class="connect chatter"><i></i>Connect with Chatterloop</div>
  <div class="connect workvine"><i></i>Connect with Workvine</div>
  <div class="home"></div>
</section>

<section class="screen s4">
  <div class="hero"></div>
  <svg class="panel-shape"><use href="#panel"/></svg>
  <div class="status"><span>9:41</span><svg><use href="#status"/></svg></div>
  <h1 class="title">MUSIC I LOVE</h1>
  <div class="badge"><svg viewBox="0 0 80 80" fill="none" stroke="#5b6173" stroke-width="4"><path d="M16 50 L6 40 Q2 34 6 30 Q11 26 16 32 Q21 26 26 30 Q30 34 26 40 Z"/><ellipse cx="36" cy="58" rx="7" ry="6"/><ellipse cx="62" cy="50" rx="7" ry="6"/><path d="M43 58 L43 24 L69 14 L69 50 M43 34 L69 24"/></svg></div>
  <div class="chips">
    <div class="chip">The Lanterns<i class="avatar" role="img" aria-label="Band portrait"></i></div>
    <div class="chip">Velora Quinn<i class="avatar" role="img" aria-label="Artist portrait"></i></div>
    <div class="chip">Nine Dimes<i class="avatar" role="img" aria-label="Artist emblem"></i></div>
    <div class="chip">Ray Holloway<i class="avatar" role="img" aria-label="Artist emblem"></i></div>
    <div class="chip wide">Brynn Sparrow<i class="avatar" role="img" aria-label="Artist emblem"></i></div>
  </div>
  <div class="connect chatter"><i></i>Connect with Chatterloop</div>
  <div class="connect tunevale"><i></i>CONNECT WITH TUNEVALE</div>
  <div class="home"></div>
</section>

</body>
</html>
```